Need a new company business card

I am looking for a new company business card. Front and back. With information on it as per below. Card should be professional. Yet clever. Simple. Modern design. Pim card, traditional size. OK with say, all black or all red backside.

Varnholt is an indie, bootstrapped magazine advancing the work of intersectional feminists busting their buts to create a just world through the power of enterprise and innovation.

Varnholt is the home and voice of entrepreneurial feminism and feminist innovators worldwide. Entrepreneurial feminists are people (of all genders) who see inequality as an innovation priority. They work to advance gender equity and/or who strive to integrate and practice feminist principles, pedagogy, values into their innovation and entrepreneurship work.
We are committed to this space being trans and queer inclusive, anti-racist, intersectional, brave, and safe. We welcome all allies. We value learning, edgy but civil discourse and integrative thinking skills.

Target Market(s)

feminists, business owners,

Industry/Entity Type

Publishing Company

Contact Information for Business Card

RD Tolliver
Founder/Publisher
4-237 Ashgrove Lane, Toronto, ON
M4T 2K8
publisher@varnholt.com
416-552-3019
www.varnholt.com

Font styles to use
Serif
Other font styles liked:
• Myriad Pro

Colors
ec1f27
000000
ffffff

Requirements
Must have
• logo
• use red, black white colours only.
Nice to have
• use the compass in pattern or creatively but not too busy please
Should not have
• Should not be too busy. Elegant.

```html
<!DOCTYPE html>
<html lang="en">
<head>
<meta charset="utf-8">
<title>Varnholt business card</title>
<link rel="stylesheet" href="https://fonts.googleapis.com/css2?family=Roboto:wght@400;500;700&display=swap">
<style>
:root{
  --backdrop:#c9c9c9;
  --ink:#171717;
  --charcoal:#34373b;
  --red:#d8211f;
  --paper:#f4f4f4;
  --white:#ffffff;
  --text:#2b2b2b;
}
*{margin:0;padding:0;box-sizing:border-box}
html,body{width:1200px;height:1138px;overflow:hidden;background:var(--backdrop)}
.stage{position:relative;width:1200px;height:1138px}
.card{position:absolute;width:620px;height:374px;border-radius:14px;overflow:hidden;font-family:"Roboto",sans-serif}
.card-front{left:274px;top:186px;background:var(--ink);border-bottom:4px solid var(--red)}
.card-back{left:276px;top:608px;background:linear-gradient(180deg,var(--white),var(--paper))}

.lockup{position:absolute;display:flex;flex-direction:column}
.card-front .lockup{left:0;right:0;top:124px;align-items:center;color:var(--white)}
.card-back .lockup{left:40px;top:130px;color:var(--charcoal)}
.wordmark{font-weight:700;letter-spacing:-1px;line-height:1}
.card-front .wordmark{font-size:84px}
.card-back .wordmark{font-size:70px}
.tagline{font-weight:500;font-size:10.5px;letter-spacing:1.1px;text-transform:uppercase;white-space:nowrap;margin-top:8px}

.band{position:absolute;left:0;top:0}
.holder{position:absolute;right:54px;top:40px;text-align:right;color:var(--white)}
.holder .name{font-size:22px;font-weight:700;line-height:1.2}
.holder .role{font-size:15px;font-weight:400;margin-top:3px}
.address{position:absolute;left:40px;top:290px;font-size:15px;line-height:20px;color:var(--text);font-style:normal}
.contacts{position:absolute;right:30px;top:268px;list-style:none;font-size:15px;color:var(--text)}
.contacts li{display:flex;justify-content:flex-end;align-items:center;gap:12px;height:20px}
.contacts svg{width:13px;height:13px;fill:var(--red)}
</style>
</head>
<body>
<main class="stage">
  <section class="card card-front" aria-label="Card front">
    <div class="lockup">
      <span class="wordmark">Varnholt</span>
      <p class="tagline">Independent notes on enterprise and equity</p>
    </div>
  </section>

  <section class="card card-back" aria-label="Card back">
    <svg class="band" width="620" height="374" viewBox="0 0 620 374" aria-hidden="true">
      <path d="M0 0H620V112C500 122 400 92 300 60C200 30 100 26 0 46Z" fill="var(--charcoal)"/>
      <path d="M0 58C100 38 200 42 300 72C400 104 500 134 620 124" fill="none" stroke="var(--red)" stroke-width="7"/>
    </svg>
    <div class="holder">
      <p class="name">RD Tolliver</p>
      <p class="role">Founder/Publisher</p>
    </div>
    <div class="lockup">
      <span class="wordmark">Varnholt</span>
      <p class="tagline">Independent notes on enterprise and equity</p>
    </div>
    <address class="address">4-237 Ashgrove Lane,<br>Toronto, ON M4T 2K8</address>
    <ul class="contacts">
      <li>416-552-3019
        <svg viewBox="0 0 16 16" aria-hidden="true"><path d="M3 1l3 1 1 3-2 1.5a9 9 0 0 0 4.5 4.5L11 9l3 1 1 3-2 2C7 15 1 9 1 3z"/></svg></li>
      <li>www.varnholt.com
        <svg viewBox="0 0 16 16" aria-hidden="true"><path d="M1 3h14v10H1z M2 4l6 5 6-5" fill="var(--red)" stroke="var(--white)" stroke-width="1"/></svg></li>
      <li>publisher@varnholt.com
        <svg viewBox="0 0 16 16" aria-hidden="true"><circle cx="8" cy="8" r="7"/><path d="M1 8h14M8 1c-3 4-3 10 0 14M8 1c3 4 3 10 0 14" fill="none" stroke="var(--white)" stroke-width="1"/></svg></li>
    </ul>
  </section>
</main>
</body>
</html>
```